New Locksmith Business needs a newspaper ad

We need an ad for a new locksmith business in Colorado called Riverbend Key Co. Our service area is located near several world-class ski resorts, which fuel the local economy. We are a comprehensive locksmith business offering automotive, commercial and residential services. We provide modern, tech-savvy digital security solutions for your home or business.

Size of ad: 3.22" x 3.44" | PDF needed for final artwork file

Target Market(s)

Local residents, businesses, hotels and resorts. As well as visitors to the area that may need emergency lock out services. High income, high net worth clients.

Industry/Entity Type

Locksmith

Font styles to use
Sans Serif

Requirements
Must have
• *Include: Logo
*Include: 970.318.2956
*Include: riverbendkeyco.com
*Include photo of Gus, he's the locksmith
*Include text: New Business!
*Include text: Auto | Residential | Commercial
*Include: Innovative Locksmith Solutions
*Colors from the logo are the main colors to use; accent color is Chrome Yellow (#ffac00)
*Bank Gothic is the headline font and we like to use Oswald font for all other text
Nice to have
• It would be nice to include another photo, in addition to the photo of Gus, if there is space. I know it is a small space, so no worries if adding another photo will not work.

```html
<!DOCTYPE html>
<html lang="en">
<head>
<meta charset="utf-8">
<title>Riverbend Key Co – New Business Ad</title>
<link href="https://fonts.googleapis.com/css2?family=Oswald:wght@400;500;600;700&display=swap" rel="stylesheet">
<style>
  :root {
    --brand-blue: #1c74bb;
    --band-blue: #3b66ad;
    --headline-blue: #3a65a8;
    --ink: #1f1f1f;
    --phone-gray: #6b6b6b;
    --chrome-yellow: #ffac00;
    --silver: #bdbdbd;
    --white: #ffffff;
    --wood-light: #c08a55;
    --wood-dark: #9a6236;
    --skin-tone: #d9b39a;
    --polo-blue: #2c5bc0;
  }
  html, body {
    margin: 0;
    padding: 0;
    width: 1149px;
    height: 1200px;
    overflow: hidden;
    background: var(--white);
  }
  .ad {
    position: relative;
    width: 1149px;
    height: 1200px;
    overflow: hidden;
    background: linear-gradient(100deg, #ffffff 0%, #ffffff 28%, #f7f5e4 38%, #eef1d9 44%);
    font-family: "Oswald", sans-serif;
  }
  .door-photo {
    position: absolute;
    left: 482px;
    top: 0;
    width: 667px;
    height: 860px;
    background: linear-gradient(90deg, #ece8df 0%, #e4ddd0 6%, var(--wood-light) 10%, #b57d4a 55%, var(--wood-dark) 100%);
  }
  .swoosh {
    position: absolute;
    left: 0;
    top: 0;
    width: 1149px;
    height: 1200px;
  }
  .brand {
    position: absolute;
    left: 52px;
    top: 52px;
    width: 400px;
    display: flex;
    flex-direction: column;
    align-items: center;
    gap: 22px;
  }
  .brand-dot {
    width: 104px;
    height: 104px;
    border-radius: 50%;
    background: var(--brand-blue);
  }
  .brand-name {
    color: var(--brand-blue);
    font-weight: 600;
    font-size: 42px;
    letter-spacing: 1px;
    line-height: 1;
    text-transform: uppercase;
    white-space: nowrap;
  }
  .headline {
    position: absolute;
    left: 71px;
    top: 300px;
    margin: 0;
    font-weight: 600;
    font-size: 86px;
    line-height: 92px;
    text-transform: uppercase;
    letter-spacing: -0.5px;
  }
  .headline .lead { color: var(--ink); display: block; }
  .headline .accent { color: var(--headline-blue); display: block; }
  .locksmith-photo {
    position: absolute;
    left: 0;
    top: 640px;
    width: 512px;
    height: 560px;
    background: linear-gradient(180deg, #c9a07f 0%, var(--skin-tone) 45%, #7d8fbf 68%, var(--polo-blue) 80%, #2853b0 100%);
  }
  .locksmith-caption {
    position: absolute;
    left: 38px;
    top: 1146px;
    color: var(--white);
    font-weight: 400;
    font-size: 27px;
    letter-spacing: 0.3px;
    white-space: nowrap;
  }
  .new-badge {
    position: absolute;
    left: 425px;
    top: 600px;
    width: 430px;
    height: 270px;
    background: var(--chrome-yellow);
    transform: rotate(-11deg);
    box-shadow: 0 18px 18px -14px rgba(0,0,0,.35);
    color: var(--white);
    text-align: center;
    text-transform: uppercase;
    font-weight: 700;
  }
  .new-badge .big { display: block; font-size: 168px; line-height: 150px; margin-top: 18px; }
  .new-badge .small { display: block; font-size: 64px; line-height: 70px; }
  .phone {
    position: absolute;
    left: 528px;
    top: 918px;
    display: flex;
    align-items: center;
    gap: 20px;
    color: var(--phone-gray);
    font-weight: 600;
    font-size: 90px;
    line-height: 1;
    white-space: nowrap;
  }
  .phone svg { width: 40px; height: 72px; }
  .web-bar {
    position: absolute;
    left: 493px;
    top: 1029px;
    width: 656px;
    height: 64px;
    background: var(--band-blue);
    border-radius: 32px 0 0 32px;
    color: var(--white);
    font-weight: 600;
    font-size: 46px;
    line-height: 64px;
    text-align: center;
    letter-spacing: 0.5px;
    text-transform: uppercase;
  }
  .services {
    position: absolute;
    left: 517px;
    top: 1110px;
    display: flex;
    align-items: center;
    color: var(--ink);
    font-weight: 500;
    font-size: 44px;
    line-height: 56px;
    white-space: nowrap;
  }
  .services .divider {
    width: 4px;
    height: 48px;
    background: var(--band-blue);
    margin: 0 20px;
  }
</style>
</head>
<body>
<main class="ad">
  <div class="door-photo" role="img" aria-label="Photo of a wooden door with a smart lock and a hand holding a phone showing a home automation app"></div>

  <svg class="swoosh" viewBox="0 0 1149 1200" aria-hidden="true">
    <path d="M0,706 Q540,520 1149,740 L1149,1200 L0,1200 Z" fill="var(--silver)"/>
    <path d="M0,752 Q560,585 1149,782 L1149,1200 L0,1200 Z" fill="var(--band-blue)"/>
    <path d="M0,790 Q560,625 1149,822 L1149,1200 L0,1200 Z" fill="var(--white)"/>
  </svg>

  <div class="brand">
    <span class="brand-dot" aria-hidden="true"></span>
    <span class="brand-name">Riverbend Key Co</span>
  </div>

  <h1 class="headline">
    <span class="lead">Innovative</span>
    <span class="accent">Locksmith</span>
    <span class="accent">Solutions</span>
  </h1>

  <div class="locksmith-photo" role="img" aria-label="Portrait photo of Gus, the locksmith, smiling in a blue polo shirt"></div>
  <div class="locksmith-caption">GUS HOLLIS, Locksmith</div>

  <div class="new-badge">
    <span class="big">New</span>
    <span class="small">Business!</span>
  </div>

  <div class="phone">
    <svg viewBox="0 0 40 72" aria-hidden="true">
      <rect x="3" y="3" width="34" height="66" rx="6" fill="none" stroke="var(--band-blue)" stroke-width="5"/>
      <rect x="8" y="12" width="24" height="44" fill="var(--band-blue)"/>
      <circle cx="20" cy="62" r="3" fill="var(--band-blue)"/>
    </svg>
    <span>970.318.2956</span>
  </div>

  <div class="web-bar">riverbendkeyco.com</div>

  <div class="services">
    <span>Auto</span><span class="divider"></span><span>Residential</span><span class="divider"></span><span>Commercial</span>
  </div>
</main>
</body>
</html>
```